Wordpress website for a new Podcast

Hi, We are looking for a designer to create a wordpress website project for a new podcast and publish it on the domain we own.

The show is called “Bright Gatherings” (logo included) and its aim is to interview guests who work as professional facilitators, trainers, teachers and coaches. The show has a positive vibe, is fun, vibrant and full of positive energy. These are the feelings we want to convey in the design.

The website should have a similar structure to: https://www.plumvesselcast.example/ with the following content:

1) The main page including:
- navigation bar and social buttons at the top
- main graphic design featuring the latest episode
- "latest episodes" section displaying 3 episodes (please design a mask to be used for new episodes when they air together with the face of the interviewee) -> this will link to the respective episodes
- please design an "bright gatherings" book cover mockup to be inluded as a banner -> this will link to Orindel
- subscribe to the newsletter - a banner capturing the name and email of the user -> to be connected to PostWren.
-> a working episode search.

2) Episodes page
- the show will be divided into seasons (12 episodes each) and each episode will need a separate "blog entry" including:
-> A short article (4-5 paragraphs) + stock image
-> interviewee's bio and social links

3) Meet the hosts page
- including bios of the two hosts of the show
- links to their social profiles
- a "request speaker availability" form which sends an email

Some additional nice-to-haves:
1) Good and clean Bio's would be awesome (both for the hosts & the interviewees),
2) an easily navigable episode system,
3) a keyword/date search option
4) easy to share options (share to WhatsApp, Facebook, Twitter, LinkedIn) 5) We must be able to track how the podcasts are shared (google analytics?)

```html
<!DOCTYPE html>
<html lang="en">
<head>
<meta charset="utf-8">
<title>Bright Gatherings</title>
<link href="https://fonts.googleapis.com/css2?family=Josefin+Sans:wght@400;600;700&family=Mulish:wght@400;600;700&display=swap" rel="stylesheet">
<style>
:root{
  --red:#f4380f;
  --red-deep:#e8300a;
  --amber:#f0a319;
  --pink:#fb5b6b;
  --coral:#ff7a45;
  --ink:#222;
  --muted:#555;
  --ring:#f6e0a8;
  --dark:#393939;
  --white:#fff;
}
*{box-sizing:border-box;margin:0;padding:0}
html,body{width:1200px;height:4392px;overflow:hidden}
body{position:relative;font-family:'Mulish',sans-serif;color:var(--ink);background:var(--white)}
.abs{position:absolute}
.heading{font-family:'Josefin Sans',sans-serif;font-weight:600;letter-spacing:1px}
.accent{color:var(--red)}
.btn{position:absolute;display:flex;align-items:center;justify-content:center;border-radius:30px;color:var(--white);font-size:18px}

/* header */
.site-header{position:absolute;left:0;top:0;width:1200px;height:119px;background:var(--red)}
.brand{position:absolute;left:94px;top:30px;display:flex;align-items:center;gap:10px;color:var(--white);font-family:'Josefin Sans',sans-serif;font-weight:700;font-size:22px}
.brand-dot{width:46px;height:46px;border-radius:50%;background:var(--amber)}
.search{position:absolute;left:656px;top:17px;width:253px;height:44px;border-radius:22px;background:var(--white);overflow:hidden}
.search span{position:absolute;left:22px;top:13px;font-size:14px;font-style:italic;color:#999}
.search i{position:absolute;right:0;top:0;width:46px;height:44px;background:var(--amber)}
.social-top{position:absolute;left:958px;top:30px;display:flex;gap:28px}
.social-top i{width:17px;height:17px;border-radius:50%;background:var(--white)}
.nav{position:absolute;top:82px;left:0;font-size:16px;color:var(--white)}
.nav span{position:absolute;white-space:nowrap}

/* hero */
.hero{position:absolute;left:0;top:119px;width:1200px;height:600px}
.hero-title{left:559px;top:112px;font-size:56px;line-height:64px;color:var(--white);font-weight:600;white-space:nowrap}
.hero-sub{left:559px;top:186px;width:560px;font-size:22px;line-height:31px;color:var(--white)}
.book{position:absolute;border-radius:6px;box-shadow:0 14px 24px rgba(0,0,0,.18)}

/* episodes */
.section-title{position:absolute;left:0;width:1200px;text-align:center;font-size:44px}
.card{position:absolute;top:900px;width:324px;height:442px;border:1px solid #d6d6d6;background:var(--white);text-align:center}
.card-media{position:absolute;left:5px;top:6px;width:312px;height:174px}
.card-pod{position:absolute;left:136px;top:153px;width:52px;height:52px;border-radius:50%;background:var(--white)}
.card-pod::after{content:"";position:absolute;left:14px;top:14px;width:24px;height:24px;border-radius:50%;border:4px solid var(--amber)}
.card-ep{position:absolute;left:0;width:100%;top:216px;font-size:17px;color:var(--muted)}
.card-title{position:absolute;left:30px;width:262px;top:250px;font-size:21px;line-height:27px;color:var(--ink)}
.card-text{position:absolute;left:20px;width:282px;top:316px;font-size:15px;line-height:25px;color:var(--muted)}
.card .btn{left:32px;top:412px;width:259px;height:56px;background:var(--red)}

/* banner */
.banner{position:absolute;left:0;top:1488px;width:1200px;height:447px;background:linear-gradient(90deg,#ef5a20 0%,#e9862a 45%,#d9a22c 100%)}

/* authors */
.author{position:absolute;top:2131px;width:200px;text-align:center}
.author-photo{width:200px;height:200px;border-radius:50%;border:7px solid var(--ring)}
.author-name{margin-top:30px;font-size:19px;letter-spacing:1px;font-family:'Josefin Sans',sans-serif}
.author-role{font-size:14px;color:#888;margin-top:4px}
.author-rule{position:absolute;right:0;top:227px;width:2px;height:36px;background:var(--red)}

/* newsletter */
.newsletter{position:absolute;left:0;top:2520px;width:1200px;height:518px;background:var(--red)}
.field{position:absolute;top:252px;height:60px;border-radius:30px;background:var(--white);font-size:17px;color:#777;padding:19px 24px}
.ring-icon{position:absolute;top:356px;width:55px;height:55px;border-radius:50%;border:2px solid var(--white)}
.ring-icon::after{content:"";position:absolute;left:19px;top:19px;width:13px;height:13px;border-radius:50%;background:var(--white)}

/* feature */
.bubble{position:absolute;width:147px;height:147px;border-radius:50%;border:2px solid #222;display:flex;flex-direction:column;align-items:center;justify-content:center;text-align:center;font-size:19px;line-height:25px;color:#333}
.bubble::before{content:"";position:absolute;inset:-7px -3px -3px -7px;border-radius:50%;border:1.5px solid #222;transform:rotate(12deg)}

/* footer */
.footer-col{position:absolute;top:4040px;font-size:13px;line-height:31.5px;color:var(--white)}
.footer-col h4{font-family:'Josefin Sans',sans-serif;font-weight:600;font-size:17px;letter-spacing:1px;margin-bottom:22px}
.footer-icons{display:flex;gap:22px;margin-top:12px}
.footer-icons i{width:12px;height:12px;border-radius:50%;background:var(--white)}
.copyright{position:absolute;left:0;top:4331px;width:1200px;text-align:center;font-size:13px;color:var(--white)}
</style>
</head>
<body>

<header class="site-header">
  <div class="brand"><span class="brand-dot"></span>Bright Gatherings</div>
  <div class="search"><span>Search Episode</span><i></i></div>
  <div class="social-top" aria-label="Social links"><i></i><i></i><i></i><i></i></div>
  <nav class="nav">
    <span style="left:477px">Home</span>
    <span style="left:561px">About</span>
    <span style="left:645px">Blog</span>
    <span style="left:717px">Podcasts</span>
    <span style="left:824px">Training</span>
    <span style="left:925px">Free Stuff</span>
    <span style="left:1038px">Webinars</span>
  </nav>
</header>

<section class="hero">
  <svg class="abs" style="left:0;top:0" width="1200" height="600" viewBox="0 0 1200 600">
    <defs>
      <linearGradient id="heroGrad" x1="0" y1="0" x2="1" y2="0.3">
        <stop offset="0" stop-color="#fb4d6a"/>
        <stop offset="0.55" stop-color="#f8483a"/>
        <stop offset="1" stop-color="#ff6a3a"/>
      </linearGradient>
    </defs>
    <rect width="1200" height="600" fill="url(#heroGrad)"/>
    <path d="M0 430 C150 390 260 520 420 470 C560 430 660 430 760 430 C880 430 980 470 1200 420 L1200 600 L0 600Z" fill="#f98c92"/>
    <path d="M0 490 C120 470 220 580 380 545 C520 515 640 470 780 520 C900 565 1040 490 1200 520 L1200 600 L0 600Z" fill="#fbc3c2"/>
    <path d="M0 540 C160 520 260 600 420 590 C560 580 700 520 860 560 C980 590 1100 520 1200 530 L1200 600 L0 600Z" fill="#fff"/>
  </svg>
  <div class="book" role="img" aria-label="Bright Gatherings book cover mockup" style="left:232px;top:70px;width:156px;height:300px;background:linear-gradient(180deg,#ff5a1f,#f7a11a)"></div>
  <div class="abs heading hero-title">BRIGHT GATHERINGS</div>
  <div class="abs hero-sub">At vero eos et accusamus et iusto odio dignissimos ducimus qui blanditiis praesentium</div>
  <div class="btn" style="left:559px;top:287px;width:247px;height:54px;background:var(--amber)">Get The Book Now »</div>
  <div class="btn" style="left:820px;top:287px;width:194px;height:54px;background:var(--red)">Get Trained »</div>
</section>

<h2 class="section-title heading" style="top:822px">LATEST <span class="accent">EPISODES</span></h2>

<article class="card" style="left:89px">
  <div class="card-media" role="img" aria-label="Episode cover with guest photo" style="background:linear-gradient(90deg,#f44a14 50%,#c9c4c2 50%)"></div>
  <div class="card-pod"></div>
  <div class="card-ep">Episode:156</div>
  <div class="card-title">Lorem ipsum dolor sit amet, consectetur</div>
  <div class="card-text">Ut enim ad minim veniam, quis nostrud exercitation ullamco laboris nisi ut aliqui</div>
  <div class="btn">Explore</div>
</article>
<article class="card" style="left:438px">
  <div class="card-media" role="img" aria-label="Episode cover with guest photo" style="background:linear-gradient(90deg,#f44a14 50%,#d9d7d4 50%)"></div>
  <div class="card-pod"></div>
  <div class="card-ep">Episode:156</div>
  <div class="card-title">Lorem ipsum dolor sit amet, consectetur</div>
  <div class="card-text">Ut enim ad minim veniam, quis nostrud exercitation ullamco laboris nisi ut aliqui</div>
  <div class="btn">Explore</div>
</article>
<article class="card" style="left:788px">
  <div class="card-media" role="img" aria-label="Episode cover with guest photo" style="background:linear-gradient(90deg,#f44a14 50%,#bdbcbc 50%)"></div>
  <div class="card-pod"></div>
  <div class="card-ep">Episode:156</div>
  <div class="card-title">Lorem ipsum dolor sit amet, consectetur</div>
  <div class="card-text">Ut enim ad minim veniam, quis nostrud exercitation ullamco laboris nisi ut aliqui</div>
  <div class="btn">Explore</div>
</article>

<section class="banner" role="img" aria-label="Speaker facing an audience in a warm orange tint">
  <div class="abs heading" style="left:104px;top:112px;font-size:44px;color:var(--white)">BRIGHT GATHERINGS</div>
  <div class="abs" style="left:80px;top:180px;width:472px;text-align:center;font-size:18px;line-height:31px;color:var(--white)">Lorem ipsum dolor sit amet, consectetur adipiscing elit,sed do eiusmod tempor</div>
  <div class="btn" style="left:188px;top:272px;width:259px;height:54px;background:var(--amber)">Register Now</div>
</section>

<h2 class="section-title heading" style="top:2046px">MEET THE <span class="accent">AUTHORS</span></h2>

<div class="author" style="left:91px"><div class="author-photo" role="img" aria-label="Portrait photo of Tessa Brook" style="background:#9c8d85"></div><div class="author-name">Tessa Brook</div><div class="author-role">Lorem ipsum</div><div class="author-rule" style="right:-1px"></div></div>
<div class="author" style="left:364px"><div class="author-photo" role="img" aria-label="Portrait photo of author" style="background:#8a7a70"></div><div class="author-name">Accusamus</div><div class="author-role">Lorem ipsum</div><div class="author-rule" style="right:-1px"></div></div>
<div class="author" style="left:637px"><div class="author-photo" role="img" aria-label="Portrait photo of author" style="background:#a8a4a0"></div><div class="author-name">Veritatis</div><div class="author-role">Lorem ipsum</div><div class="author-rule" style="right:-1px"></div></div>
<div class="author" style="left:909px"><div class="author-photo" role="img" aria-label="Portrait photo of author" style="background:#9a6f60"></div><div class="author-name">Denouncing</div><div class="author-role">Lorem ipsum</div><div class="author-rule" style="right:-1px"></div></div>

<section class="newsletter">
  <h2 class="section-title heading" style="top:100px;color:var(--white)">SUBSCRIBE OUR NEWSLETTER</h2>
  <p class="abs" style="left:250px;top:170px;width:700px;text-align:center;font-size:17px;line-height:29px;color:var(--white)">Lorem ipsum dolor sit amet, consectetur adipiscing elit, sed do eiusmod tempor incididunt ut labore et dolore magna aliqua</p>
  <div class="field" style="left:90px;width:420px">User Name</div>
  <div class="field" style="left:522px;width:421px">Email Address</div>
  <div class="btn" style="left:956px;top:252px;width:154px;height:60px;background:var(--amber);font-weight:700;font-size:19px">Subscribe</div>
  <span class="ring-icon" style="left:464px"></span>
  <span class="ring-icon" style="left:536px"></span>
  <span class="ring-icon" style="left:607px"></span>
  <span class="ring-icon" style="left:679px"></span>
</section>

<h2 class="section-title heading" style="top:3158px">BRIGHT <span class="accent">GATHERINGS</span></h2>
<p class="abs" style="left:250px;top:3226px;width:700px;text-align:center;font-size:19px;line-height:31px;color:var(--muted)">Lorem ipsum dolor sit amet, consectetur adipiscing elit, sed do eiusmod tempor incididunt ut labore et dolore magna aliqua</p>

<div class="book" role="img" aria-label="Bright Gatherings book mockup" style="left:527px;top:3355px;width:148px;height:292px;background:linear-gradient(180deg,#ff5a1f,#f7a11a)"></div>

<div class="bubble" style="left:200px;top:3325px">Just<span style="color:var(--red);font-size:23px">17.00</span></div>
<div class="bubble" style="left:856px;top:3325px">See<br>Our Details</div>
<div class="bubble" style="left:145px;top:3530px">Look<br>Inside</div>
<div class="bubble" style="left:908px;top:3530px">Our<br>Merchandise</div>

<svg class="abs" style="left:0;top:3380px" width="1200" height="240" viewBox="0 0 1200 240" fill="none" stroke="#222" stroke-width="3" stroke-linecap="round">
  <path d="M435 63 C410 65 390 55 375 35 M375 35 l2 14 M375 35 l13 4"/>
  <path d="M765 63 C790 65 810 55 825 35 M825 35 l-2 14 M825 35 l-13 4"/>
  <path d="M380 150 C355 150 335 160 322 180 M322 180 l1 -14 M322 180 l13 -5"/>
  <path d="M820 150 C845 150 865 160 878 180 M878 180 l-1 -14 M878 180 l-13 -5"/>
</svg>

<svg class="abs" style="left:0;top:3780px" width="1200" height="612" viewBox="0 0 1200 612">
  <path d="M0 80 C140 70 230 0 360 20 C480 40 540 80 680 60 C800 40 900 40 1040 70 C1110 85 1160 75 1200 70 L1200 612 L0 612Z" fill="#4a4a4a"/>
  <path d="M0 110 C120 100 240 60 380 80 C520 100 620 120 760 100 C900 80 1020 110 1200 100 L1200 612 L0 612Z" fill="#414141"/>
  <path d="M0 140 L1200 140 L1200 612 L0 612Z" fill="var(--dark)"/>
</svg>

<div class="footer-col" style="left:90px"><h4>COMPANY</h4>Home<br>About<br>Blog<br>Podcasts<br>Training<br>Free Stuff<br>Webinars</div>
<div class="footer-col" style="left:326px"><h4>CONTACT</h4>Faq<br>Legal<br>Privacy Policy<br>Terms &amp; Conditions</div>
<div class="footer-col" style="left:614px;line-height:25px"><h4 style="margin-bottom:26px">ADDRESS</h4>18 Larkspur Lane<br>Fenmoor, OR 97000<br>USA<br><div style="margin-top:8px">(555) 014-2290<br>hello@brightgatherings.example</div></div>
<div class="footer-col" style="left:946px;line-height:27px"><h4 style="margin-bottom:22px">MY ACCOUNT</h4>Log in<br>Sign Up<h4 style="margin:30px 0 0">FOLLOW US</h4><div class="footer-icons"><i></i><i></i><i></i><i></i></div></div>

<div class="copyright">© 2019 The company Name. All rights Reserved</div>

</body>
</html>
```